Business Card Design Project

Basic business card with minimal details. I just need company name, email & web address, telephone and my name.
I would like the back of the card to be grey with my logo & company name centred.

Target Market(s)

Architects
Builders
Property Developers

Industry/Entity Type

Business

Font styles to use
Sans Serif

Colors

Designer to choose colors to be used in the design.

Requirements
Must have
• Tallow Crest
Rupert Hazelby - Director
M: 0427 915203
E: rupert@tallowcrest.com.au
W: www.tallowcrest.com.au
Should not have
• No other images or pictures

```html
<!DOCTYPE html>
<html lang="en">
<head>
<meta charset="utf-8">
<title>Tallow Crest – Business Card Front</title>
<link rel="stylesheet" href="https://fonts.googleapis.com/css2?family=Open+Sans:wght@400;600;700&display=swap">
<style>
  :root {
    --backdrop: #ececec;
    --card: #ffffff;
    --brand-red: #a51c30;
    --slate: #4a5562;
    --text-grey: #4f5660;
    --card-shadow: rgba(0, 0, 0, 0.14);
  }
  * { box-sizing: border-box; margin: 0; padding: 0; }
  html, body {
    width: 1200px;
    height: 864px;
    overflow: hidden;
    background: var(--backdrop);
    font-family: "Open Sans", Arial, sans-serif;
  }
  .stage {
    position: relative;
    width: 1200px;
    height: 864px;
    display: flex;
    align-items: center;
    justify-content: center;
  }
  .card {
    position: relative;
    width: 900px;
    height: 540px;
    background: var(--card);
    box-shadow: 0 14px 40px var(--card-shadow);
  }
  .brand {
    position: absolute;
    top: 78px;
    left: 0;
    right: 0;
    display: flex;
    flex-direction: column;
    align-items: center;
    gap: 26px;
  }
  .brand-square {
    width: 74px;
    height: 74px;
    background: var(--brand-red);
  }
  .brand-name {
    font-size: 46px;
    font-weight: 600;
    letter-spacing: 0.08em;
    color: var(--slate);
    text-transform: uppercase;
    line-height: 1;
  }
  .person {
    position: absolute;
    top: 270px;
    left: 0;
    right: 0;
    display: flex;
    align-items: flex-start;
  }
  .divider {
    flex: 1;
    height: 3px;
    background: var(--slate);
    margin-top: 22px;
  }
  .person-block {
    padding: 0 16px;
    text-align: center;
    color: var(--brand-red);
  }
  .person-name {
    font-size: 30px;
    font-weight: 700;
    letter-spacing: 0.04em;
    text-transform: uppercase;
    line-height: 1.4;
  }
  .person-title {
    font-size: 20px;
    font-weight: 400;
    line-height: 1.1;
  }
  .contact {
    position: absolute;
    top: 378px;
    left: 0;
    right: 0;
    list-style: none;
    text-align: center;
    color: var(--text-grey);
    font-size: 22px;
    line-height: 44px;
    letter-spacing: 0.02em;
  }
</style>
</head>
<body>
  <main class="stage">
    <article class="card card-front">
      <header class="brand">
        <div class="brand-square" aria-hidden="true"></div>
        <div class="brand-name">Tallow Crest</div>
      </header>
      <section class="person">
        <span class="divider"></span>
        <div class="person-block">
          <div class="person-name">Rupert Hazelby</div>
          <div class="person-title">Director</div>
        </div>
        <span class="divider"></span>
      </section>
      <ul class="contact">
        <li class="contact-phone">0427 915203</li>
        <li class="contact-email">rupert@tallowcrest.com.au</li>
        <li class="contact-web">www.tallowcrest.com.au</li>
      </ul>
    </article>
  </main>
</body>
</html>
```